Business Card Design

Online clothing womens clothing store, I sell my clothing online and at the markets.

i would like the attached picture on the front of the card and the contact information on the back.

Industry/Entity Type

Business

Contact Information for Business Card

Marlow Thread
Karen Whitfield
(Instagram symbol) _marlow_thread_
(Facebook symbol) www.fakebookexample.com/marlowthreadau/

W : www.marlowthread.example.au
E : info@marlowthread.example.au
P : 0498716204

```html
<!DOCTYPE html>
<html lang="en">
<head>
<meta charset="utf-8">
<title>Marlow Thread – Business Card</title>
<link href="https://fonts.googleapis.com/css2?family=Open+Sans:wght@400;600&display=swap" rel="stylesheet">
<style>
  :root {
    --page-bg: #e4e4e4;
    --card-light: #f2f2f2;
    --card-mid: #d4d4d4;
    --brand-blue: #3a56a5;
    --brand-black: #0a0a0a;
    --ink: #1b1b1b;
    --white: #ffffff;
    --photo-light: #d8dedd;
    --photo-teal: #bfcccc;
    --photo-dark: #5b6064;
    --wordmark-pale: #e9e9e6;
  }
  * { box-sizing: border-box; margin: 0; padding: 0; }
  html, body {
    width: 1189px; height: 1200px; overflow: hidden;
    background: var(--page-bg);
    font-family: "Open Sans", Arial, sans-serif;
  }
  .card {
    position: absolute; left: 136px; width: 916px; height: 524px;
    overflow: hidden;
    box-shadow: 4px 6px 12px rgba(0,0,0,0.25);
  }
  .card--contact { top: 45px; background: linear-gradient(180deg, var(--card-mid) 0%, var(--card-light) 45%, var(--card-mid) 100%); }
  .card--photo { top: 625px; }

  .wordmark {
    position: absolute; top: 92px; left: 0; width: 100%;
    text-align: center; font-size: 42px; font-weight: 400;
    letter-spacing: 0.28em; color: var(--ink);
  }
  .waves { position: absolute; inset: 0; }
  .holder-name {
    position: absolute; left: 60px; top: 360px;
    font-size: 46px; color: var(--white); font-weight: 400;
  }
  .divider {
    position: absolute; left: 428px; top: 314px; width: 3px; height: 182px;
    background: var(--white);
  }
  .contact-list { position: absolute; left: 460px; top: 314px; list-style: none; }
  .contact-list li {
    display: flex; align-items: center; height: 37px;
    color: var(--white); font-size: 23px;
  }
  .contact-list svg { width: 26px; height: 26px; margin-right: 32px; flex: none; }

  .photo-fill {
    position: absolute; inset: 0;
    background: linear-gradient(100deg, var(--photo-light) 0%, var(--photo-teal) 38%, #8d9599 58%, var(--photo-dark) 80%, #6f7478 100%);
  }
  .photo-wordmark {
    position: absolute; left: 58px; top: 362px;
    font-size: 86px; font-weight: 600; letter-spacing: 0.04em;
    color: var(--wordmark-pale); white-space: nowrap;
  }
</style>
</head>
<body>
  <section class="card card--contact">
    <svg class="waves" viewBox="0 0 916 524" aria-hidden="true">
      <path fill="var(--brand-black)" d="M0,216 C120,250 180,285 260,280 C400,270 560,205 690,215 C790,222 860,255 916,287 L916,289 C860,255 780,225 690,229 C560,235 400,330 243,335 C140,338 60,320 0,305 Z"/>
      <path fill="var(--brand-blue)" stroke="#e8e8e8" stroke-width="2" d="M0,305 C60,320 140,338 243,335 C400,330 560,235 690,229 C780,225 860,255 916,289 L916,530 L0,530 Z"/>
    </svg>
    <div class="wordmark">MARLOW THREAD</div>
    <div class="holder-name">Karen Whitfield</div>
    <div class="divider"></div>
    <ul class="contact-list">
      <li>
        <svg viewBox="0 0 26 26"><rect width="26" height="26" fill="#fff"/><path d="M9 5c-2 1-3 3-2 6 1 4 4 8 8 10 2 1 4 0 5-2l-3-3-2 1c-2-1-4-4-5-6l1-2z" fill="var(--brand-blue)"/></svg>
        0498716204
      </li>
      <li>
        <svg viewBox="0 0 26 26"><rect width="26" height="26" fill="#fff"/><rect x="4" y="7" width="18" height="12" fill="var(--brand-blue)"/><path d="M4 7l9 7 9-7" stroke="#fff" stroke-width="1.5" fill="none"/></svg>
        info@marlowthread.example.au
      </li>
      <li>
        <svg viewBox="0 0 26 26"><rect width="26" height="26" fill="#fff"/><circle cx="13" cy="13" r="9" fill="var(--brand-blue)"/><path d="M4 13h18M13 4c-4 4-4 14 0 18M13 4c4 4 4 14 0 18" stroke="#fff" stroke-width="1.2" fill="none"/></svg>
        www.marlowthread.example.au
      </li>
      <li>
        <svg viewBox="0 0 26 26"><rect x="2" y="2" width="22" height="22" fill="none" stroke="#fff" stroke-width="3"/></svg>
        marlow_thread
      </li>
      <li>
        <svg viewBox="0 0 26 26"><rect width="26" height="26" fill="#fff"/></svg>
        www.fakebookexample.com
      </li>
    </ul>
  </section>

  <section class="card card--photo">
    <div class="photo-fill" role="img" aria-label="Atmospheric photograph of a woman in soft misty grey and teal tones"></div>
    <div class="photo-wordmark">MARLOW THREAD</div>
  </section>
</body>
</html>
```